KRL Stationery Design Project

Dear Designers,
We need a new stationery design for company to match our new logo.
Designers should provide a design for the following:
1. Business Card: 3.5x2 Inches.
2. Letterhead: A4 size.
3. Envelops: 25x35.5 Cm.
You can keep the Arabic name at the bottom of the logo Or you can use the separate attached Arabic Name.
Please refer to the attached logo guide for design information.
Sample Business Card information:
Name: Tarek Sowan
Position: Operation Manager
Tel: +966 920007164 Ex. 500
Fax: +966 (3)8842617
Mob: +966 (5)00263817
email: tarek@krl-example.com.sa
URL: www.krl-example.com.sa
Address:
Nakheel Heights, Suite 718
Zayed bin Omar Str.
Khobar, 31847
Saudi Arabia
Updates
Dear All,
Please note, we had uploaded our logo along with Arabic writing in Adobe illustrator format (.ai).
Regards,
Karim
Dear All,
A sample data for the business card had been added as per your request.
Regards,
Karim

```html
<!DOCTYPE html>
<html lang="en">
<head>
<meta charset="utf-8">
<title>KRL Business Card</title>
<link href="https://fonts.googleapis.com/css2?family=Source+Sans+3:ital,wght@0,400;0,600;0,700;1,700&display=swap" rel="stylesheet">
<style>
  :root {
    --navy: #13305a;
    --grey: #9b9b9c;
    --paper: #ffffff;
    --backdrop: #2a2a2c;
    --ink: #2c2c2c;
  }
  html, body {
    margin: 0;
    padding: 0;
    width: 960px;
    height: 1200px;
    overflow: hidden;
    background: var(--backdrop);
    font-family: "Source Sans 3", "Myriad Pro", sans-serif;
  }
  .card {
    position: absolute;
    left: 57px;
    width: 840px;
    height: 480px;
    background: var(--paper);
    border-radius: 30px;
    overflow: hidden;
  }
  .card--front { top: 80px; }
  .card--back { top: 625px; height: 478px; }

  .card__waves {
    position: absolute;
    left: 0;
    top: 0;
    width: 840px;
    height: 480px;
    display: block;
  }

  .brand {
    position: absolute;
    display: flex;
    align-items: center;
    gap: 18px;
    color: var(--navy);
    font-weight: 700;
    line-height: 1;
  }
  .brand__mark {
    background: var(--grey);
    border-radius: 50%;
  }
  .card--front .brand {
    left: 70px;
    top: 92px;
    font-size: 92px;
    letter-spacing: 2px;
  }
  .card--front .brand__mark { width: 34px; height: 34px; }
  .card--back .brand {
    left: 0;
    right: 0;
    top: 175px;
    justify-content: center;
    font-size: 130px;
    letter-spacing: 3px;
  }
  .card--back .brand__mark { width: 46px; height: 46px; }

  .divider {
    position: absolute;
    left: 513px;
    top: 88px;
    width: 1px;
    height: 124px;
    background: #8c8c8c;
  }

  .contact {
    position: absolute;
    left: 541px;
    top: 83px;
    color: var(--navy);
  }
  .contact__name {
    margin: 0;
    font-size: 28px;
    font-weight: 400;
    line-height: 1.1;
  }
  .contact__role {
    margin: 3px 0 0 2px;
    font-size: 20px;
    line-height: 1.2;
  }
  .contact__lines {
    margin: 14px 0 0 0;
    padding: 0;
    list-style: none;
    font-size: 20px;
    line-height: 28px;
  }
  .contact__lines b { font-style: italic; font-weight: 700; }
  .contact__address {
    margin: 12px 0 0 -2px;
    font-style: normal;
    font-size: 20px;
    line-height: 28px;
    color: var(--ink);
  }

  .footer {
    position: absolute;
    left: 0;
    right: 0;
    top: 432px;
    margin: 0;
    text-align: center;
    color: var(--paper);
    font-size: 20px;
    line-height: 28px;
    padding-left: 26px;
  }
  .footer b { font-style: italic; font-weight: 700; }
  .footer__sep { margin: 0 10px; }
</style>
</head>
<body>

<section class="card card--front">
  <svg class="card__waves" viewBox="0 0 840 480" preserveAspectRatio="none" aria-hidden="true">
    <path d="M540,401 C690,398 800,340 850,250 L850,310 C790,372 680,401 540,401 Z" fill="var(--grey)"/>
    <path d="M-10,440 C130,400 300,388 440,393 C600,398 740,385 850,316 L850,490 L-10,490 Z" fill="var(--navy)"/>
    <path d="M-10,440 C130,400 300,388 440,393 C600,398 740,385 850,316" fill="none" stroke="var(--paper)" stroke-width="4"/>
  </svg>

  <div class="brand"><span>KRL</span><span class="brand__mark"></span></div>

  <div class="divider"></div>

  <div class="contact">
    <h1 class="contact__name">Your Name</h1>
    <p class="contact__role">Designation</p>
    <ul class="contact__lines">
      <li><b>t</b> : 123-123-1234</li>
      <li><b>f</b> : 123-123-1234</li>
    </ul>
    <address class="contact__address">1234, Suite# 123<br>Street Name<br>Country Code</address>
  </div>

  <p class="footer"><b>e</b> : info@krl-example.com.sa<span class="footer__sep">|</span><b>w</b> : www.krl-example.com.sa</p>
</section>

<section class="card card--back">
  <div class="brand"><span>KRL</span><span class="brand__mark"></span></div>
</section>

</body>
</html>
```